Book Cover Project

This is a printed journal front and back cover design. We like the current design, but it feels a little too flat / too simple.

NOTE: we are not looking for a total makeover, just a finishing / polishing of this cover.

Here is our other book cover: https://www.shelvora-books.example/Quiet-Studio-Ledger-Fine-Morning/dp/7093268415/ref=tmm_hrd_swatch_0?_encoding=UTF8&qid=&sr=
it's purple and yellow (mostly purple)
this one is yellow and we're thinking to add a purple bar at the bottom

Specs: 6 in x 9 in full bleed for print

```html
<!DOCTYPE html>
<html lang="en">
<head>
<meta charset="utf-8">
<title>Winding Distance Notebook – Front Cover</title>
<link rel="stylesheet" href="https://fonts.googleapis.com/css2?family=Bebas+Neue&family=Oswald:wght@400&family=Montserrat:wght@400;600&display=swap">
<style>
  :root {
    --backdrop: #f1f1f1;
    --cover-yellow: #fdd92b;
    --ink: #111111;
    --violet: #855aa3;
    --figure-tone-a: rgba(17, 17, 17, 0.16);
    --figure-tone-b: rgba(17, 17, 17, 0.06);
  }
  * { margin: 0; padding: 0; box-sizing: border-box; }
  html, body {
    width: 1200px;
    height: 800px;
    overflow: hidden;
    background: var(--backdrop);
  }
  .canvas {
    position: relative;
    width: 1200px;
    height: 800px;
  }
  .book-cover {
    position: absolute;
    left: 340px;
    top: 66px;
    width: 462px;
    height: 690px;
    background: var(--cover-yellow);
  }
  .book-cover svg { display: block; width: 100%; height: 100%; }
  .title-light {
    font-family: "Oswald", "Arial Narrow", sans-serif;
    font-weight: 400;
    font-size: 103px;
    fill: var(--ink);
  }
  .title-bold {
    font-family: "Bebas Neue", "Arial Narrow", sans-serif;
    font-size: 108px;
    fill: var(--violet);
  }
  .tagline {
    font-family: "Montserrat", Arial, sans-serif;
    font-weight: 600;
    font-size: 19px;
    fill: var(--ink);
  }
  .author {
    font-family: "Montserrat", Arial, sans-serif;
    font-weight: 400;
    font-size: 24px;
    fill: var(--violet);
  }
  .base-band { fill: var(--violet); }
</style>
</head>
<body>
<main class="canvas">
  <section class="book-cover" aria-label="Winding Distance Notebook front cover">
    <svg viewBox="0 0 462 690" xmlns="http://www.w3.org/2000/svg">
      <defs>
        <linearGradient id="runner-fill" x1="0" y1="0" x2="0" y2="1">
          <stop offset="0" stop-color="var(--figure-tone-a)"/>
          <stop offset="1" stop-color="var(--figure-tone-b)"/>
        </linearGradient>
      </defs>

      <g class="title-block">
        <text class="title-light" x="53" y="232" textLength="50" lengthAdjust="spacingAndGlyphs">W</text>
        <rect class="runner-figure" x="107" y="145" width="36" height="95" rx="4"
              fill="url(#runner-fill)" role="img"
              aria-label="Single-line drawing of a runner standing in for the letter I"/>
        <text class="title-light" x="151" y="232" textLength="251" lengthAdjust="spacingAndGlyphs">NDING</text>

        <text class="title-bold" x="53" y="325" textLength="349" lengthAdjust="spacingAndGlyphs">DISTANCE</text>

        <text class="title-light" x="53" y="418" textLength="349" lengthAdjust="spacingAndGlyphs">NOTEBOOK</text>
      </g>

      <text class="tagline" x="231" y="456" text-anchor="middle">Run - Write - Transform</text>

      <text class="author" x="231" y="632" text-anchor="middle" textLength="255" lengthAdjust="spacing">DANIEL ASHGROVE</text>

      <rect class="base-band" x="0" y="678" width="462" height="12"/>
    </svg>
  </section>
</main>
</body>
</html>
```